Bramwell Corner Sports Pub. Where the locals go!!

We are creating a sports pub. We are needing a fun website that offers our menu along with an event page and general info. We have some attached links that we really like:
https://www.dunmorrows.example/
https://www.cafepelindra.example/
https://www.quillstoneyx.example/
We are doing a pirate theme but that is because the area we are in. We would like to see a pirate like in our logo doing something like drinking real time similar to the dunmorrows website above.
Target Market(s)
Sports Fans
Industry/Entity Type
Pub, Bar, Restaurant
Coding
Coded - Design and coding required
Number of Pages Required
3 page
Font styles to use
Other font styles liked:
- see uploads
Look and feel

```html
<!DOCTYPE html>
<html lang="en">
<head>
<meta charset="utf-8">
<title>Bramwell Corner Sports Pub</title>
<link rel="stylesheet" href="https://fonts.googleapis.com/css2?family=Rye&family=Lato:ital,wght@0,400;0,700;1,400&display=swap">
<style>
:root{
  --cream:#ece5c3;
  --cream-card:#e9e0b8;
  --teal:#6dbfa7;
  --terra:#c9705a;
  --ink:#141414;
  --white:#ffffff;
  --display:'Rye', serif;
  --body:'Lato', sans-serif;
}
*{box-sizing:border-box;margin:0;padding:0}
html,body{width:1200px;height:3411px;overflow:hidden}
body{position:relative;background:var(--cream);font-family:var(--body);color:var(--ink)}
.abs{position:absolute}
.display{font-family:var(--display);font-weight:400;text-transform:uppercase}

/* nav */
.site-nav{position:absolute;left:0;top:0;width:1200px;height:70px;background:var(--cream);z-index:5}
.nav-link{position:absolute;top:26px;font-size:15px;color:var(--ink);text-decoration:none}
.btn{position:absolute;display:flex;align-items:center;justify-content:center;background:var(--teal);color:var(--white);border-radius:30px;font-family:var(--display);text-transform:uppercase;letter-spacing:1px;text-decoration:none}
.nav-brand{position:absolute;left:488px;top:0;width:225px;height:100px;background:var(--cream);border-radius:0 0 60px 60px;z-index:6;display:flex;align-items:center;justify-content:center;gap:8px;padding-bottom:12px}
.brand-dot{width:34px;height:34px;border-radius:50%;background:var(--terra);flex:none}
.brand-name{font-family:var(--display);font-size:13px;line-height:15px;color:var(--ink);text-transform:uppercase}

/* hero */
.hero{position:absolute;left:0;top:70px;width:1200px;height:720px;background:linear-gradient(180deg,#0b0b0b 0%,#2b2a26 35%,#4b3b32 62%,#5a4538 78%,var(--cream) 100%)}
.hero-photo{position:absolute;inset:0;background:radial-gradient(ellipse at 60% 30%,rgba(60,110,70,.35),transparent 55%)}
.hero-title{position:absolute;left:0;top:160px;width:1200px;text-align:center;color:var(--white);font-size:47px;line-height:62px;letter-spacing:1px}
.hero-copy{position:absolute;left:270px;top:293px;width:660px;text-align:center;color:var(--white);font-size:15px;line-height:25px}

/* menu */
.section-title{position:absolute;left:0;width:1200px;text-align:center;font-size:38px;color:var(--ink)}
.menu-circle{position:absolute;width:274px;height:274px;border-radius:50%;overflow:hidden}
.menu-photo{position:absolute;inset:0}
.menu-tab{position:absolute;left:30px;bottom:-40px;width:214px;height:130px;border-radius:50%;background:var(--teal);color:var(--white);text-align:center;padding-top:34px;font-size:19px}
.menu-feature{background:var(--terra);color:var(--white);text-align:center}
.menu-feature h3{margin-top:78px;font-size:24px}
.menu-feature p{width:210px;margin:14px auto 0;font-size:15px;line-height:26px}
.menu-feature a{display:block;margin-top:10px;font-family:var(--display);font-size:12px;color:var(--teal);text-decoration:none;text-transform:uppercase}
.deco{position:absolute;opacity:.35}

/* about */
.about{position:absolute;left:0;top:1324px;width:1200px;height:620px;background:var(--terra)}
.about-frame{position:absolute;left:106px;top:67px;width:476px;height:476px;border-radius:50%;border:10px solid var(--white);background:linear-gradient(160deg,#8a3a22,#3e1e16 60%,#a65a3c)}
.about-title{position:absolute;left:634px;top:108px;font-size:38px;color:var(--ink)}
.about-copy{position:absolute;left:635px;width:445px;font-size:15px;line-height:26px;color:#2a1a14}

/* events */
.event-card{position:absolute;width:302px;background:var(--cream-card);border-radius:32px;box-shadow:0 6px 24px rgba(120,100,50,.12)}
.event-photo{position:absolute;width:268px;height:276px;border-radius:40px 10px 40px 10px}
.event-body{position:absolute;left:30px;width:250px}
.event-date{font-family:var(--display);font-size:13px;color:var(--teal)}
.event-title{margin-top:12px;font-family:var(--display);font-size:19px;line-height:33px;text-transform:uppercase;color:var(--ink)}
.event-text{margin-top:12px;font-size:14px;line-height:26px}
.event-more{display:block;margin-top:8px;font-family:var(--display);font-size:13px;color:var(--terra);text-decoration:none;text-transform:uppercase}

/* footer */
.footer-fade{position:absolute;left:0;top:2770px;width:1200px;height:110px;background:linear-gradient(180deg,var(--cream),#000)}
.footer{position:absolute;left:0;top:2880px;width:1200px;height:531px;background:#000;color:var(--white)}
.footer-brand{position:absolute;left:468px;top:75px;display:flex;align-items:center;gap:16px}
.footer-brand .brand-dot{width:58px;height:58px}
.footer-brand .brand-name{font-size:23px;line-height:27px;color:var(--teal)}
.social{position:absolute;top:250px;width:32px;height:32px;border-radius:50%;background:var(--terra)}
.contact-icon{position:absolute;top:338px;width:46px;height:46px;border-radius:50%;display:flex;align-items:center;justify-content:center}
.contact-text{position:absolute;font-size:15px;line-height:25px}
.contact-label{font-family:var(--display);font-size:12px}
.copyright{position:absolute;left:0;top:453px;width:1200px;text-align:center;font-size:14px}
.copyright span{color:var(--teal)}
</style>
</head>
<body>

<nav class="site-nav">
  <a class="nav-link" href="#" style="left:135px">Home</a>
  <a class="nav-link" href="#" style="left:213px">About Us</a>
  <a class="nav-link" href="#" style="left:313px">Our Menu</a>
  <a class="nav-link" href="#" style="left:776px">Events</a>
  <a class="nav-link" href="#" style="left:872px">Faq</a>
  <a class="btn" href="#" style="left:926px;top:17px;width:164px;height:36px;font-size:15px">Conatct Us</a>
</nav>
<div class="nav-brand">
  <span class="brand-dot"></span>
  <span class="brand-name">Bramwell Corner<br>Sports Pub</span>
</div>

<header class="hero">
  <div class="hero-photo" role="img" aria-label="Photo of cheering sports fans watching a game in the pub"></div>
  <h1 class="hero-title display">Welcome to<br>Bramwell Corner Sports Pub</h1>
  <p class="hero-copy">Lorem ipsum dolor sit amet, consectetur adipiscing elit, sed do eiusmod tempor incididunt ut labore et dolore magna aliqua. Quis ipsum suspendisse ultrices gravida.</p>
  <a class="btn" href="#" style="left:505px;top:376px;width:189px;height:44px;font-size:16px">Conatct Us</a>
</header>

<h2 class="section-title display" style="top:840px">Our Menu</h2>
<div class="deco" role="img" aria-label="Decorative compass illustration" style="left:1110px;top:795px;width:90px;height:172px;border-radius:86px 0 0 86px;background:#9a9478"></div>
<div class="deco" role="img" aria-label="Decorative ship anchor illustration" style="left:29px;top:1137px;width:123px;height:175px;border-radius:12px;background:#a29c80"></div>

<div class="menu-circle" style="left:137px;top:942px">
  <div class="menu-photo" role="img" aria-label="Photo of the colourful pub bar with memorabilia" style="background:linear-gradient(160deg,#5a3b2a,#c8843f 45%,#4c2a22)"></div>
  <div class="menu-tab display">Lorem Ipsum</div>
</div>
<div class="menu-circle menu-feature" style="left:463px;top:942px">
  <h3 class="display">Lorem Ipsum</h3>
  <p>Lorem ipsum dolor sit amet, consectetur adipiscing elit, sed do eiusmod</p>
  <a href="#">Learn More &raquo;</a>
</div>
<div class="menu-circle" style="left:788px;top:942px">
  <div class="menu-photo" role="img" aria-label="Photo of leather booth seating under framed sports pictures" style="background:linear-gradient(180deg,#4a2c22,#6b3a26 55%,#8a4a2a)"></div>
  <div class="menu-tab display">Lorem Ipsum</div>
</div>

<section class="about">
  <div class="about-frame" role="img" aria-label="Photo of guests gathered at the bar"></div>
  <div class="abs" role="img" aria-label="Pirate mascot illustration" style="left:444px;top:252px;width:145px;height:289px;border-radius:70px 70px 20px 20px;background:linear-gradient(180deg,#3c2a22,#a8322a 45%,#2f5e3a)"></div>
  <h2 class="about-title display">About Us</h2>
  <p class="about-copy" style="top:177px">Lorem ipsum dolor sit amet, consectetur adipiscing elit, sed do eiusmod tempor incididunt ut labore et dolore magna aliqua. Quis ipsum suspendisse ultrices gravida. Risus commodo viverra maecenas accumsan lacus vel facilisis.</p>
  <p class="about-copy" style="top:305px">Lorem ipsum dolor sit amet, consectetur adipiscing elit, sed do eiusmod tempor incididunt ut labore et dolore magna aliqua. Quis ipsum suspendisse ultrices gravida. Risus commodo viverra maecenas accumsan lacus vel facilisis.</p>
  <a class="btn" href="#" style="left:632px;top:434px;width:208px;height:58px;font-size:18px">Learn More</a>
</section>

<h2 class="section-title display" style="top:2040px">Our Events</h2>
<div class="deco" role="img" aria-label="Decorative pirate skull and crossed swords illustration" style="left:0;top:2609px;width:170px;height:133px;border-radius:60px 60px 10px 10px;background:#3a3a34;opacity:.6"></div>

<article class="event-card" style="left:127px;top:2342px;height:338px">
  <div class="event-body" style="top:118px">
    <div class="event-date"><i style="font-family:var(--body)">12 04 2022 &nbsp;12:42 PM</i></div>
    <div class="event-title">Lorem Ipsum<br>Dolor Sit Amet</div>
    <p class="event-text">Lorem ipsum dolor sit amet, consectetur adipiscing elit</p>
    <a class="event-more" href="#">Learn More</a>
  </div>
</article>
<div class="event-photo" role="img" aria-label="Photo of the long wooden bar with screens" style="left:144px;top:2150px;background:linear-gradient(180deg,#3a4a6a,#6a4a2e 50%,#8a5a30)"></div>

<article class="event-card" style="left:449px;top:2150px;height:530px">
  <div class="event-body" style="top:38px">
    <div class="event-date">12 04 2022 &nbsp;12:42 PM</div>
    <div class="event-title">Lorem Ipsum<br>Dolor Sit Amet</div>
    <p class="event-text">Lorem ipsum dolor sit amet, consectetur adipiscing elit</p>
    <a class="event-more" href="#">Learn More</a>
  </div>
</article>
<div class="event-photo" role="img" aria-label="Photo of a crowd enjoying drinks in the pub" style="left:466px;top:2404px;background:linear-gradient(170deg,#7a2a1a,#3a1a14 55%,#8a4a34)"></div>

<article class="event-card" style="left:770px;top:2342px;height:338px">
  <div class="event-body" style="top:118px">
    <div class="event-date">12 04 2022 &nbsp;12:42 PM</div>
    <div class="event-title">Lorem Ipsum<br>Dolor Sit Amet</div>
    <p class="event-text">Lorem ipsum dolor sit amet, consectetur adipiscing elit</p>
    <a class="event-more" href="#">Learn More</a>
  </div>
</article>
<div class="event-photo" role="img" aria-label="Photo of the bar interior with stools and arcade machine" style="left:787px;top:2150px;background:linear-gradient(160deg,#b8463a,#d0943c 45%,#2a3a5a)"></div>

<div class="footer-fade" aria-hidden="true"></div>
<footer class="footer">
  <div class="footer-brand">
    <span class="brand-dot"></span>
    <span class="brand-name">Bramwell Corner<br>Sports Pub</span>
  </div>
  <a class="social" href="#" aria-label="Social link" style="left:513px"></a>
  <a class="social" href="#" aria-label="Social link" style="left:558px"></a>
  <a class="social" href="#" aria-label="Social link" style="left:605px"></a>
  <a class="social" href="#" aria-label="Social link" style="left:650px"></a>

  <div class="contact-icon" style="left:228px;background:var(--terra)">
    <svg width="18" height="22" viewBox="0 0 18 22"><path fill="#fff" d="M9 0C4 0 0 4 0 9c0 6 9 13 9 13s9-7 9-13C18 4 14 0 9 0zm0 12a3 3 0 110-6 3 3 0 010 6z"/></svg>
  </div>
  <p class="contact-text" style="left:287px;top:333px">Bramwell Corner Sports Pub<br>Lorem ipsum dolor<br>sit amet</p>

  <div class="contact-icon" style="left:480px;background:var(--teal)">
    <svg width="20" height="20" viewBox="0 0 24 24"><path fill="#fff" d="M6.6 10.8a15.2 15.2 0 006.6 6.6l2.2-2.2a1 1 0 011-.25 11.4 11.4 0 003.6.6 1 1 0 011 1V20a1 1 0 01-1 1A17 17 0 013 4a1 1 0 011-1h3.5a1 1 0 011 1c0 1.25.2 2.45.6 3.6a1 1 0 01-.25 1z"/></svg>
  </div>
  <div class="contact-text" style="left:542px;top:335px"><div class="contact-label">Phone</div>+1 888 888 8888</div>

  <div class="contact-icon" style="left:711px;background:var(--terra)">
    <svg width="20" height="16" viewBox="0 0 20 16"><path fill="#fff" d="M0 2a2 2 0 012-2h16a2 2 0 012 2v.5L10 8 0 2.5zm0 2.8l10 5.5 10-5.5V14a2 2 0 01-2 2H2a2 2 0 01-2-2z"/></svg>
  </div>
  <div class="contact-text" style="left:778px;top:338px"><div class="contact-label">Email</div>info@bramwellcornerpub.example</div>

  <p class="copyright">&copy; copyrights 2023 &nbsp;<span>Bramwell Corner Sports Pub</span> | &nbsp;&nbsp;&nbsp; All rights reserved.</p>
</footer>

</body>
</html>
```